Tidewell Comforts, a portable luxury restroom trailer company needs a landing page

We need a landing page for a luxury portable restroom trailer company. This should be modern, and simple - use any combination of Pantone colors: Warm Gray 1C, Black 7C, 7529c, 873C, 8003C

We rent these trailers for special events like weddings, private parties, festivals, family reunions, team building, wine tastings, beer tastings, food truck round-ups, etc.

An idea of the landing page is in the files below. Please use stock photography and placeholder text for now. The winning design will be given final content.

Requirements
Must have
• Multiple "Get Quote" buttons or a place for them to type in type of rental, how many people etc

```html
<!DOCTYPE html>
<html lang="en">
<head>
<meta charset="utf-8">
<title>Tidewell Comforts – Luxury Restroom Trailers</title>
<link href="https://fonts.googleapis.com/css2?family=Poppins:wght@400;500;600;700;800&family=Inter:wght@400;500&display=swap" rel="stylesheet">
<style>
:root{
  --gold:#e9b320;
  --brown:#ad8462;
  --brown-deep:#8a6a4c;
  --link:#b8863b;
  --ink:#1f1f1f;
  --text:#555555;
  --muted:#8a8a8a;
  --line:#e4e4e4;
  --white:#ffffff;
  --paper:#ffffff;
}
*{box-sizing:border-box;margin:0;padding:0}
html,body{width:1200px;height:3715px;overflow:hidden}
body{font-family:"Inter",Arial,sans-serif;color:var(--ink);background:var(--paper);position:relative}
.abs{position:absolute}
.btn{position:absolute;display:flex;align-items:center;justify-content:center;background:var(--gold);color:#222;font-family:"Poppins",Arial,sans-serif;font-weight:600;font-size:14px;border-radius:6px;letter-spacing:.2px}
.photo{position:absolute;border:5px solid rgba(255,255,255,.85)}

/* hero */
.hero{position:absolute;left:0;top:0;width:1200px;height:639px;background:linear-gradient(110deg,#b99674 0%,#a58260 45%,#8f7155 100%);overflow:hidden}
.hero-door{position:absolute;left:0;top:270px;width:45px;height:210px;background:#7f9b80;opacity:.6}
.brand{position:absolute;display:flex;align-items:center;gap:12px;font-family:"Poppins",Arial,sans-serif;font-weight:700;font-size:18px;line-height:21px;letter-spacing:1px}
.brand .mark{width:40px;height:40px;border-radius:4px;flex:none}
.hero .brand{left:111px;top:15px;color:var(--white)}
.hero .brand .mark{background:var(--white)}
.nav a{position:absolute;top:30px;color:#fbefe0;font-family:"Poppins",Arial,sans-serif;font-size:14px;text-decoration:none}
.search{position:absolute;left:812px;top:22px;width:126px;height:30px;border-bottom:1px solid rgba(255,255,255,.6);color:#fbefe0;font-size:14px}
.search svg{position:absolute;right:0;top:2px}
.hero-eyebrow{left:111px;top:188px;color:var(--white);font-family:"Poppins",Arial,sans-serif;font-weight:400;font-size:44px;letter-spacing:.5px}
.hero-title{left:106px;top:250px;color:var(--white);font-family:"Poppins",Arial,sans-serif;font-weight:800;font-size:74px;line-height:92px}
.hero-copy{left:110px;top:450px;width:460px;color:#fbefe0;font-size:14px;line-height:26px}

/* section heads */
.eyebrow{position:absolute;left:0;width:1200px;text-align:center;font-family:"Poppins",Arial,sans-serif}
h2.eyebrow{font-weight:600;font-size:30px}
.rule{position:absolute;left:560px;top:810px;width:80px;height:2px;background:var(--brown)}

/* event cards */
.event{position:absolute;width:476px;height:232px;background:var(--white);box-shadow:0 2px 10px rgba(0,0,0,.12);border-radius:4px;overflow:hidden}
.event .pic{position:absolute;left:0;top:0;width:213px;height:232px}
.event h3{position:absolute;left:236px;top:26px;font-family:"Poppins",Arial,sans-serif;font-weight:500;font-size:18px;letter-spacing:.4px}
.event p{position:absolute;left:236px;top:66px;width:218px;font-size:14px;line-height:26px;color:var(--text);text-align:justify}
.event a{position:absolute;left:236px;top:184px;font-size:15px;color:var(--link);font-weight:500;text-decoration:none}

/* about */
.about{position:absolute;left:0;top:1527px;width:1200px;height:514px;background:linear-gradient(90deg,#2b3a22 0%,#495040 25%,#7b7b75 45%,#9a9a96 60%,#5c5c58 78%,#0d0d0d 90%,#1b2a14 100%)}
.about-box{position:absolute;left:111px;top:88px;width:397px;height:361px;border-radius:22px;background:linear-gradient(110deg,#e9e9e9 0%,#d4d4d4 45%,#9a9a9a 85%,#bcbcbc 100%);border:1px solid #ddd;text-align:center}
.about-box h2{margin-top:28px;font-family:"Poppins",Arial,sans-serif;font-weight:600;font-size:27px;line-height:42px;color:#2a2a2a}
.about-box p{margin:14px auto 0;width:350px;font-size:14.5px;line-height:26px;color:#2f2f2f}

/* products */
.product{position:absolute;top:2269px;width:310px;height:353px;background:var(--white);border-radius:18px;box-shadow:0 2px 12px rgba(0,0,0,.13);overflow:hidden}
.product .pic{height:179px}
.product h3{margin:24px 20px 0;font-family:"Poppins",Arial,sans-serif;font-weight:500;font-size:18px;line-height:23px;color:#2d3148}
.product p{margin:18px 20px 0;font-size:14.5px;line-height:23px;color:var(--muted)}
.dots{display:flex;gap:6px;margin:14px 22px}
.dots i{width:6px;height:6px;border-radius:50%;background:var(--gold);opacity:.8}
.dots i:nth-child(2){opacity:.45}

/* contact */
.contact{position:absolute;left:0;top:2709px;width:1200px;height:653px;background:var(--brown)}
.field{position:absolute;background:var(--white);border-radius:5px;font-size:13px;color:#666;display:flex;align-items:center;padding-left:15px}
.field svg{position:absolute;right:16px;top:50%;margin-top:-4px}

/* footer */
.footer h4{position:absolute;top:3438px;font-family:"Poppins",Arial,sans-serif;font-weight:500;font-size:21px;color:var(--ink)}
.footer ul{position:absolute;list-style:none;font-size:15px;line-height:26px;color:#333}
.footer li::before{content:"\203A";color:#999;margin-right:10px}
.social{position:absolute;top:3542px;width:38px;height:38px;border-radius:50%;background:#e6e6e6}
.cinfo{position:absolute;left:840px;font-size:15px;line-height:26px;color:#333;display:flex;gap:12px}
</style>
</head>
<body>

<header class="hero">
  <div class="hero-door" role="img" aria-label="Restroom trailer side with door in the background"></div>
  <div class="brand"><span class="mark"></span><span>TIDEWELL<br>COMFORTS</span></div>
  <nav class="nav">
    <a style="left:378px">HOME</a>
    <a style="left:480px">EVENT</a>
    <a style="left:586px">PRODUCT</a>
    <a style="left:712px">CONTACT</a>
  </nav>
  <div class="search">Search
    <svg width="14" height="14" viewBox="0 0 14 14" fill="none" stroke="#fbefe0" stroke-width="2"><circle cx="6" cy="6" r="4.5"/><path d="M9.5 9.5L13 13"/></svg>
  </div>
  <div class="btn" style="left:974px;top:14px;width:111px;height:50px">LOG IN</div>

  <div class="abs hero-eyebrow">WELCOME TO</div>
  <h1 class="abs hero-title">TIDEWELL<br>COMFORTS</h1>
  <p class="abs hero-copy">Lorem ipsum dolor sit amet, consectetur adipiscing elit, sed do v incididunt ut labore et dolore magna aliqua.</p>
  <div class="btn" style="left:111px;top:522px;width:154px;height:51px">REQUEST QUOTE</div>

  <div class="photo" style="left:562px;top:72px;width:257px;height:257px;background:linear-gradient(135deg,#3b3530,#1b1a1d 60%,#5e5a55)" role="img" aria-label="Bride and groom celebrating at their wedding"></div>
  <div class="photo" style="left:819px;top:118px;width:173px;height:175px;background:linear-gradient(160deg,#6b6057,#3a3331)" role="img" aria-label="Wedding couple embracing"></div>
  <div class="photo" style="left:992px;top:89px;width:208px;height:161px;background:linear-gradient(180deg,#9a8f63,#e5e3dc 60%,#8a8760)" role="img" aria-label="Restroom trailer parked outdoors"></div>
  <div class="photo" style="left:643px;top:262px;width:202px;height:159px;background:linear-gradient(180deg,#7fa4cf,#dadde0 60%,#7c8a56)" role="img" aria-label="Trailer at an event site"></div>
  <div class="photo" style="left:845px;top:288px;width:150px;height:145px;background:linear-gradient(180deg,#5d94d2,#dfe4e8 70%,#6d8c4a)" role="img" aria-label="Trailers at a festival field"></div>
  <div class="photo" style="left:1018px;top:250px;width:182px;height:128px;background:linear-gradient(135deg,#8a6d55,#3c2d26)" role="img" aria-label="Friends laughing at a party"></div>
  <div class="photo" style="left:588px;top:421px;width:217px;height:218px;background:linear-gradient(180deg,#9aa3a8,#e6e6e4 60%,#7d7c78)" role="img" aria-label="Food truck at a round-up"></div>
  <div class="photo" style="left:805px;top:440px;width:179px;height:199px;background:linear-gradient(135deg,#6f6965,#caa24a 60%,#3a3838)" role="img" aria-label="Friends dancing at a festival"></div>
  <div class="photo" style="left:984px;top:378px;width:216px;height:261px;background:linear-gradient(135deg,#5a3b2b,#b37e52 55%,#3d2b22)" role="img" aria-label="Guests at a wine tasting"></div>
</header>

<section class="events">
  <div class="eyebrow" style="top:730px;font-size:21px">Our Events</div>
  <h2 class="eyebrow" style="top:760px">Sed ut perspiciatis unde omnis</h2>
  <div class="rule"></div>

  <article class="event" style="left:111px;top:867px">
    <div class="pic" style="background:linear-gradient(135deg,#4b6b2f,#2c63b8 50%,#333)" role="img" aria-label="Blue portable toilet on a trailer"></div>
    <h3>WEDDINGS</h3>
    <p>Lorem ipsum dolor sit amet, consectetur adipiscing elit, sed do eiusmod tempor incididunt eiusmod tempor incididunt</p>
    <a>Read More</a>
  </article>
  <article class="event" style="left:611px;top:867px">
    <div class="pic" style="background:linear-gradient(135deg,#6f7f63,#2f8357 50%,#4a4a48)" role="img" aria-label="Green portable toilets on a truck"></div>
    <h3>PRIVATE PARTIES</h3>
    <p>Lorem ipsum dolor sit amet, consectetur adipiscing elit, sed do eiusmod tempor incididunt eiusmod tempor incididunt</p>
    <a>Read More</a>
  </article>
  <article class="event" style="left:111px;top:1124px">
    <div class="pic" style="background:linear-gradient(90deg,#5d6f80,#8b97a3 40%,#d98b3a 55%,#4a5866)" role="img" aria-label="Metal restroom stalls at a festival"></div>
    <h3>FESTIVALS</h3>
    <p>Lorem ipsum dolor sit amet, consectetur adipiscing elit, sed do eiusmod tempor incididunt eiusmod tempor incididunt</p>
    <a>Read More</a>
  </article>
  <article class="event" style="left:611px;top:1124px">
    <div class="pic" style="background:linear-gradient(135deg,#7a3b2d,#8b6246 50%,#4d3626)" role="img" aria-label="Wooden barrel restroom trailer"></div>
    <h3>FAMILY REUNIONS</h3>
    <p>Lorem ipsum dolor sit amet, consectetur adipiscing elit, sed do eiusmod tempor incididunt eiusmod tempor incididunt</p>
    <a>Read More</a>
  </article>

  <div class="btn" style="left:524px;top:1389px;width:157px;height:52px">SEE MORE BLOG</div>
  <div class="abs" style="left:949px;top:1411px;width:234px;height:115px;border-radius:8px;background:linear-gradient(90deg,#cfe3f2,#ffffff 70%,#e6e6e6)" role="img" aria-label="Illustration of a restroom trailer truck"></div>
</section>

<section class="about" role="img" aria-label="Silver restroom trailer with steps at night">
  <div class="about-box">
    <h2>ABOUT TIDEWELL<br>COMFORTS</h2>
    <p>Lorem ipsum dolor sit amet, consectetur adipiscing elit, sed do eiusmod tempor incididunt ut labore et dolore magna aliqua. Ut enim ad minim veniam, quis nostrud exercitation ullamco laboris nisi ut aliquip ex ea commodo consequat.</p>
    <div class="btn" style="left:133px;top:263px;width:138px;height:51px">LEARN MORE</div>
  </div>
</section>

<section class="products">
  <h2 class="eyebrow" style="top:2117px">Our Products</h2>
  <p class="eyebrow" style="top:2178px;font-family:Inter,Arial,sans-serif;font-size:14.5px;line-height:26px;color:#333">Lorem ipsum dolor sit amet, consectetur adipiscing elit, sed do eiusmod<br>tempor incididunt ut labore et dolore magna aliqua.</p>

  <article class="product" style="left:111px">
    <div class="pic" style="background:linear-gradient(180deg,#6d6257,#d5d5d2 50%,#3f3d3a)" role="img" aria-label="Compact restroom trailer"></div>
    <h3>Sed ut perspiciatis unde omnis iste natus error sit</h3>
    <p>Lorem ipsum dolor sit amet, consectetur adipiscing elit, sed do</p>
    <div class="dots"><i></i><i></i><i></i></div>
  </article>
  <article class="product" style="left:445px">
    <div class="pic" style="background:linear-gradient(90deg,#b9b2a8,#efedea 45%,#7a4c33)" role="img" aria-label="Restroom trailer interior"></div>
    <h3>Sed ut perspiciatis unde omnis iste natus error sit</h3>
    <p>Lorem ipsum dolor sit amet, consectetur adipiscing elit, sed do</p>
    <div class="dots"><i></i><i></i><i></i></div>
  </article>
  <article class="product" style="left:779px">
    <div class="pic" style="background:linear-gradient(180deg,#f0f0f0,#cfcfcf 60%,#8d8d8d)" role="img" aria-label="Row of white restroom trailers with steps"></div>
    <h3>Sed ut perspiciatis unde omnis iste natus error sit</h3>
    <p>Lorem ipsum dolor sit amet, consectetur adipiscing elit, sed do</p>
    <div class="dots"><i></i><i></i><i></i></div>
  </article>

  <div class="abs" style="left:0;top:2593px;width:101px;height:116px;border-radius:0 8px 8px 0;background:linear-gradient(90deg,#cfe3f2,#ffffff)" role="img" aria-label="Illustration of a restroom trailer truck"></div>
</section>

<section class="contact">
  <div class="eyebrow" style="top:65px;color:var(--white);font-size:14px;font-weight:500">CONTACT US</div>
  <h2 class="eyebrow" style="top:87px;color:var(--white)">Contact us for a Quote</h2>

  <div class="field" style="left:313px;top:158px;width:282px;height:51px">Name</div>
  <div class="field" style="left:605px;top:158px;width:281px;height:51px">Email</div>
  <div class="field" style="left:313px;top:219px;width:573px;height:55px">Phone</div>
  <div class="field" style="left:313px;top:284px;width:282px;height:52px">Type of Event?
    <svg width="13" height="8" viewBox="0 0 13 8" fill="none" stroke="#777" stroke-width="1.5"><path d="M1 1l5.5 5.5L12 1"/></svg></div>
  <div class="field" style="left:605px;top:284px;width:281px;height:52px">How Many People?
    <svg width="13" height="8" viewBox="0 0 13 8" fill="none" stroke="#777" stroke-width="1.5"><path d="M1 1l5.5 5.5L12 1"/></svg></div>
  <div class="field" style="left:313px;top:347px;width:573px;height:55px">Type of Product Your Intersted in?
    <svg width="13" height="8" viewBox="0 0 13 8" fill="none" stroke="#777" stroke-width="1.5"><path d="M1 1l5.5 5.5L12 1"/></svg></div>
  <div class="field" style="left:313px;top:412px;width:282px;height:52px">When do you need it?</div>
  <div class="field" style="left:605px;top:412px;width:281px;height:52px">For how Long?</div>
  <div class="field" style="left:313px;top:474px;width:573px;height:55px">Where?</div>
  <div class="btn" style="left:534px;top:545px;width:132px;height:44px">SUBMIT NOW</div>
</section>

<footer class="footer">
  <div class="brand" style="left:111px;top:3455px;color:var(--brown-deep)"><span class="mark" style="background:var(--brown)"></span><span>TIDEWELL<br>COMFORTS</span></div>
  <span class="social" style="left:111px"></span>
  <span class="social" style="left:162px"></span>
  <span class="social" style="left:214px"></span>
  <span class="social" style="left:266px"></span>

  <h4 style="left:398px">QUICK LINK</h4>
  <ul style="left:398px;top:3479px"><li>Home</li><li>Event</li><li>Product</li><li>Contact</li></ul>

  <h4 style="left:626px">EVENTS</h4>
  <ul style="left:626px;top:3479px"><li>Weddings</li><li>Private Parties</li><li>Festivals</li><li>Family Reunions</li><li>Team Building</li></ul>

  <h4 style="left:839px">CONTACT US</h4>
  <div class="cinfo" style="top:3480px">
    <svg width="12" height="16" viewBox="0 0 12 16" style="margin-top:5px"><path d="M6 0a6 6 0 0 0-6 6c0 4.5 6 10 6 10s6-5.5 6-10a6 6 0 0 0-6-6z" fill="#222"/><circle cx="6" cy="6" r="2.2" fill="#fff"/></svg>
    <span>Lorem ipsum dolor sit amet,<br>consectetur adipiscing elit, sed</span></div>
  <div class="cinfo" style="top:3550px">
    <svg width="14" height="14" viewBox="0 0 24 24" style="margin-top:6px"><path fill="#222" d="M6.6 10.8a15.1 15.1 0 0 0 6.6 6.6l2.2-2.2c.3-.3.7-.4 1-.2 1.1.4 2.3.6 3.6.6.6 0 1 .4 1 1V20c0 .6-.4 1-1 1A17 17 0 0 1 3 4c0-.6.4-1 1-1h3.5c.6 0 1 .4 1 1 0 1.3.2 2.5.6 3.6.1.3 0 .7-.2 1z"/></svg>
    <span>+1 (555) 014 2280</span></div>
  <div class="cinfo" style="top:3588px">
    <svg width="15" height="12" viewBox="0 0 15 12" style="margin-top:8px"><rect width="15" height="12" rx="1" fill="#222"/><path d="M1 1.5l6.5 5 6.5-5" stroke="#fff" stroke-width="1.3" fill="none"/></svg>
    <span>info@tidewellcomforts.com</span></div>

  <svg class="abs" style="left:1154px;top:3441px" width="44" height="40" viewBox="0 0 44 40"><path d="M22 2C10 2 2 9 2 18c0 5 3 9 7 12l-2 8 9-5c2 .5 4 .7 6 .7 12 0 20-7 20-16S34 2 22 2z" fill="#fff" stroke="#ddd"/><circle cx="14" cy="18" r="2.5" fill="#555"/><circle cx="22" cy="18" r="2.5" fill="#555"/><circle cx="30" cy="18" r="2.5" fill="#555"/></svg>

  <div class="abs" style="left:111px;top:3643px;width:977px;height:1px;background:var(--line)"></div>
  <div class="abs" style="left:111px;top:3664px;font-size:13px;color:#333">©Copyrights 2022 Tidewell Comforts</div>
  <div class="abs" style="left:877px;top:3664px;font-size:13px;color:#333">Privacy Policy | Terms &amp; condtions</div>
</footer>

</body>
</html>
```